NEW Modern Sleek Business Card for VR Language Startup

Our startup is using VR to lead the next wave of world language education. We need a two-sided business card that introduces the larger organization (Brightloom Language Inc) and our contact info on one side and shows the product, Glimwoorld, on the other side.

Side 1 (contact info)= Brightloom Logo and Contact info (name, title, phone, email)

Side 2 (product)= Glimworld logo, text, and website
Text= Culturally Immersive Language Learning Games
Website= www.glimworld-play.com

Target Market(s)

Education, Technology

Contact Information for Business Card

Contact info will be updated upon approval of the design. For now, put this as a placeholder.

Perry Dunmore
Founder & CEO
pdunmore@quillpost-mail.net
(555)-014-2286

Font styles to use
Other font styles liked:
• Gibson and Century Gothic are the brand fonts

Requirements
Nice to have
• I would love to see cohesion between the design and colors of the two logos. I have attached a few business card designs that I like, so you can get a feel for my preferred style.

```html
<!DOCTYPE html>
<html lang="en">
<head>
<meta charset="utf-8">
<title>Brightloom Language – Business Card</title>
<link rel="stylesheet" href="https://fonts.googleapis.com/css2?family=Didact+Gothic&display=swap">
<style>
  :root {
    --bg: #c9c9c9;
    --card: #1e1e1f;
    --card-edge: #4d7cc7;
    --accent: #5a8be0;
    --text: #d9d9d9;
    --muted: #bdbdbd;
    --logo: #e6e6e6;
    --deco: #2a2a2b;
  }
  * { box-sizing: border-box; margin: 0; padding: 0; }
  html, body { width: 1200px; height: 1000px; overflow: hidden; }
  body {
    background: var(--bg);
    font-family: "Didact Gothic", "Century Gothic", sans-serif;
    position: relative;
  }
  .card {
    position: absolute;
    left: 220px;
    width: 760px;
    height: 434px;
    background: var(--card);
    border: 6px solid var(--card-edge);
    overflow: hidden;
  }
  .card--product { top: 50px; }
  .card--contact { top: 516px; }

  .deco {
    position: absolute;
    width: 300px; height: 300px;
    border-radius: 50%;
    background: var(--deco);
  }
  .card--product .deco { left: -120px; top: 150px; }
  .card--contact .deco { right: -90px; top: -140px; }

  /* Product side */
  .product-logo {
    position: absolute; right: 60px; top: 52px;
    display: flex; align-items: center; gap: 14px;
    color: var(--accent); font-size: 30px; letter-spacing: 1px;
  }
  .logo-dot {
    width: 22px; height: 22px; border-radius: 50%;
    background: var(--accent);
  }
  .product-info {
    position: absolute; right: 48px; top: 262px;
    text-align: right;
  }
  .site-row { display: flex; align-items: center; gap: 22px; justify-content: flex-end; }
  .site-line { width: 250px; height: 12px; display: block; }
  .site { color: var(--text); font-size: 19px; letter-spacing: 1.5px; }
  .site .hl { color: var(--accent); }
  .tagline { color: var(--muted); font-size: 19px; letter-spacing: 0.8px; margin-top: 14px; }

  /* Contact side */
  .brand {
    position: absolute; left: 52px; top: 60px;
    display: flex; align-items: center; gap: 16px;
    color: var(--logo); font-size: 36px; letter-spacing: 4px;
  }
  .brand .logo-dot { width: 26px; height: 26px; background: var(--accent); }
  .person { position: absolute; left: 56px; bottom: 88px; }
  .person-name { color: var(--accent); font-size: 40px; letter-spacing: 1px; }
  .person-title { color: var(--text); font-size: 20px; letter-spacing: 3px; margin-top: 16px; }
  .contact-list {
    position: absolute; right: 46px; bottom: 90px;
    list-style: none; text-align: right;
  }
  .contact-list li {
    display: flex; align-items: center; justify-content: flex-end; gap: 26px;
    color: var(--text); font-size: 19px; letter-spacing: 2px;
  }
  .contact-list li + li { margin-top: 22px; }
  .contact-list svg { width: 26px; height: 26px; fill: var(--accent); }
</style>
</head>
<body>

<section class="card card--product" aria-label="Product side">
  <div class="deco" role="img" aria-label="Faint decorative brand motif"></div>
  <div class="product-logo"><span class="logo-dot"></span><span>Glimworld</span></div>
  <div class="product-info">
    <div class="site-row">
      <svg class="site-line" viewBox="0 0 250 12" aria-hidden="true">
        <circle cx="6" cy="6" r="4.5" fill="none" stroke="#5a8be0" stroke-width="2"/>
        <line x1="10.5" y1="6" x2="250" y2="6" stroke="#5a8be0" stroke-width="2"/>
      </svg>
      <span class="site">www.<span class="hl">glimworld-play</span>.com</span>
    </div>
    <p class="tagline">Culturally Immersive Language Learning Games</p>
  </div>
</section>

<section class="card card--contact" aria-label="Contact side">
  <div class="deco" role="img" aria-label="Faint decorative brand motif"></div>
  <div class="brand"><span class="logo-dot"></span><span>Brightloom Language</span></div>
  <div class="person">
    <p class="person-name">Perry Dunmore</p>
    <p class="person-title">Founder | CEO</p>
  </div>
  <ul class="contact-list">
    <li>(555)-014-2286
      <svg viewBox="0 0 24 24" aria-label="Phone"><path d="M6.6 10.8a15.1 15.1 0 0 0 6.6 6.6l2.2-2.2a1 1 0 0 1 1-.25 11.4 11.4 0 0 0 3.6.57 1 1 0 0 1 1 1V20a1 1 0 0 1-1 1A17 17 0 0 1 3 4a1 1 0 0 1 1-1h3.5a1 1 0 0 1 1 1c0 1.25.2 2.45.57 3.57a1 1 0 0 1-.25 1z"/></svg>
    </li>
    <li>pdunmore@quillpost-mail.net
      <svg viewBox="0 0 24 24" aria-label="Email"><path d="M2 5h20v2l-10 6L2 7z M2 9l10 6 10-6v10H2z"/></svg>
    </li>
  </ul>
</section>

</body>
</html>
```